U.S. Popcorn company needs business cards

We are a popcorn company that manufactures popcorn and sells it to grocery stores worldwide. Our theme is "Americana" and our logo is U.S. route 66 which is the most famous highway in the U.S.

We would like the design to be simple and to use both sides. On the back side we would like to see just the logo and website. The front would be normal details

Target Market(s)

Wholesalers, grocers and distributors

Industry/Entity Type

Manufacture

Contact Information for Business Card

Business name: Prairie Lantern Popcorn
Phone: +1 555 308 4726
Email: Dale@prairielanternpopcorn.com
website: www.prairielanternpopcorn.com
Tag Line: "POPular for a reason"
Name: Dale Whitcombe
Title: Founder/President

Requirements
Must have
• Either this design should be fun or clean and simple. I will let you show me your thougths.
Nice to have
• Anything that ties in the real Hwy Route 66.
• Colors might need to be red, white and blue incorporated.
Should not have
• Not be too busy.

```html
<!DOCTYPE html>
<html lang="en">
<head>
<meta charset="utf-8">
<title>Prairie Lantern Popcorn – Business Card</title>
<link href="https://fonts.googleapis.com/css2?family=Lato:wght@400;700;900&display=swap" rel="stylesheet">
<style>
  :root {
    --backdrop: #ececec;
    --card: #ffffff;
    --navy: #0f2a6b;
    --red: #e31e2a;
    --ink: #1c1c1c;
    --divider: #3a3a3a;
    --photo-light: #efe9e4;
    --photo-mid: #e2d6c8;
    --photo-warm: #d9c08a;
  }
  * { margin: 0; padding: 0; box-sizing: border-box; }
  html, body {
    width: 1200px;
    height: 586px;
    overflow: hidden;
    background: var(--backdrop);
    font-family: "Lato", sans-serif;
  }
  .canvas {
    position: relative;
    width: 1200px;
    height: 586px;
  }
  .card {
    position: absolute;
    top: 129px;
    width: 502px;
    height: 301px;
    background: var(--card);
    overflow: hidden;
  }
  .card--back { left: 61px; }
  .card--front { left: 619px; }

  .product-photo {
    position: absolute;
    inset: 0;
    background:
      radial-gradient(ellipse 90px 120px at 42% 55%, var(--photo-warm) 0%, rgba(217,192,138,0) 100%),
      linear-gradient(180deg, var(--photo-light) 0%, var(--photo-mid) 100%);
  }

  .brand-name {
    position: absolute;
    left: 18px;
    top: 100px;
    width: 200px;
    text-align: center;
    color: var(--navy);
    font-weight: 900;
    font-size: 27px;
    line-height: 1.12;
    text-transform: uppercase;
  }

  .divider {
    position: absolute;
    left: 232px;
    top: 58px;
    width: 2px;
    height: 196px;
    background: linear-gradient(180deg, rgba(58,58,58,0) 0%, var(--divider) 50%, rgba(58,58,58,0) 100%);
  }

  .person {
    position: absolute;
    left: 251px;
    top: 82px;
  }
  .person__name {
    color: var(--red);
    font-weight: 900;
    font-size: 17px;
    line-height: 1.2;
  }
  .person__title {
    color: var(--ink);
    font-size: 11.5px;
    margin-top: 2px;
  }

  .contact {
    position: absolute;
    left: 251px;
    top: 158px;
    list-style: none;
  }
  .contact__item {
    display: flex;
    align-items: center;
    height: 24.5px;
    font-size: 11.5px;
    font-weight: 700;
    color: var(--ink);
  }
  .contact__icon {
    width: 12px;
    height: 12px;
    margin-right: 9px;
    flex: none;
  }

  .footer-bands {
    position: absolute;
    left: 0;
    bottom: 0;
    width: 502px;
    height: 16px;
  }
</style>
</head>
<body>
<main class="canvas">

  <section class="card card--back">
    <div class="product-photo" role="img" aria-label="Photo of a red and white striped popcorn box filled with popcorn on a white plate, branded with the company name"></div>
  </section>

  <section class="card card--front">
    <div class="brand-name">Prairie Lantern Popcorn</div>

    <div class="divider"></div>

    <div class="person">
      <div class="person__name">Dale Whitcombe</div>
      <div class="person__title">Founder/President</div>
    </div>

    <ul class="contact">
      <li class="contact__item">
        <svg class="contact__icon" viewBox="0 0 12 12" aria-hidden="true">
          <path d="M1 4.2 C1 2.6 3 1.8 6 1.8 C9 1.8 11 2.6 11 4.2 L9 4.8 L8.4 3.6 C7 3.2 5 3.2 3.6 3.6 L3 4.8 Z" fill="var(--navy)"/>
          <rect x="2.2" y="5.6" width="7.6" height="5" rx="0.8" fill="var(--navy)"/>
          <circle cx="6" cy="8.1" r="1.3" fill="#fff"/>
        </svg>
        +1 555 308 4726
      </li>
      <li class="contact__item">
        <svg class="contact__icon" viewBox="0 0 12 12" aria-hidden="true">
          <rect x="0.5" y="2.5" width="11" height="7.5" fill="var(--navy)"/>
          <path d="M0.8 2.8 L6 7 L11.2 2.8" fill="none" stroke="#fff" stroke-width="0.9"/>
        </svg>
        Dale@prairielanternpopcorn.com
      </li>
      <li class="contact__item">
        <svg class="contact__icon" viewBox="0 0 12 12" aria-hidden="true">
          <g fill="none" stroke="var(--navy)" stroke-width="1.5" stroke-linecap="round">
            <path d="M5 7 L7 5"/>
            <path d="M6.2 3.2 L7.4 2 A2 2 0 0 1 10 4.6 L8.8 5.8"/>
            <path d="M5.8 8.8 L4.6 10 A2 2 0 0 1 2 7.4 L3.2 6.2"/>
          </g>
        </svg>
        www.prairielanternpopcorn.com
      </li>
    </ul>

    <svg class="footer-bands" viewBox="0 0 502 16" preserveAspectRatio="none" aria-hidden="true">
      <path d="M0 3 H300 L300 16 H0 Z" fill="var(--navy)"/>
      <path d="M302 16 C306 6 312 1 322 1 H502 V16 Z" fill="var(--red)"/>
    </svg>
  </section>

</main>
</body>
</html>
```